Harbourline Physiotherapy business card design

We need a fresh, new business card design for our physiotherapy clinic Harbourline Physiotherapy

Will attach logo soon we had logo designed from our last project

Industry/Entity Type

Physical Therapy

Contact Information for Business Card

On front
Needs our logo, contact details:
58 Wexley Lane Corvale NSW 2784
Ph/f: 02 9481 2057
info@harbourlinephysio.example.com.au

Requirements
Must have
• On the back of the card needs to have area to write down follow up appointments
• On front
• Needs our logo
• The colours have to be the colours in our logo which are: sky blue, black and white
• Font to be same as our logo please
• We want the card to look simple, not too cluttered but to the point
Should not have
• We don't need any extra pictures other than our logo

```html
<!DOCTYPE html>
<html lang="en">
<head>
<meta charset="utf-8">
<title>Harbourline Physiotherapy – Business Card</title>
<link href="https://fonts.googleapis.com/css2?family=Exo+2:wght@400;700&display=swap" rel="stylesheet">
<style>
  :root {
    --backdrop: #2b2b2d;
    --blue-light: #4a8fcb;
    --blue-mid: #3a6fc0;
    --blue-deep: #2d3fa6;
    --ink: #16243f;
    --brand-blue: #1f5fb8;
    --paper: #ffffff;
    --paper-shade: #f1f2f5;
    --text-grey: #4a4d55;
    --rule: #a9acb3;
  }
  * { margin: 0; padding: 0; box-sizing: border-box; }
  html, body {
    width: 1200px; height: 900px; overflow: hidden;
    background: var(--backdrop);
    font-family: "Exo 2", sans-serif;
  }
  .stage { position: relative; width: 1200px; height: 900px; }

  .card {
    position: absolute;
    width: 620px; height: 354px;
    border-radius: 26px;
    overflow: hidden;
    box-shadow: 0 18px 40px rgba(0,0,0,0.45);
  }

  /* Back of card */
  .card-back {
    left: 120px; top: 70px;
    background: radial-gradient(ellipse at 30% 70%, var(--blue-light) 0%, var(--blue-mid) 45%, var(--blue-deep) 100%);
  }
  .card-back .brand-name {
    position: absolute; left: 50px; top: 120px;
    font-weight: 700; font-size: 50px; line-height: 1.0;
    color: var(--ink);
  }

  /* Front of card */
  .card-front {
    left: 460px; top: 470px;
    background: linear-gradient(160deg, var(--paper) 0%, var(--paper) 60%, var(--paper-shade) 100%);
  }
  .brand {
    position: absolute; left: 34px; top: 150px;
    display: flex; align-items: center; gap: 12px;
  }
  .brand-dot {
    width: 30px; height: 30px; border-radius: 50%;
    background: var(--brand-blue);
  }
  .brand .brand-name {
    font-weight: 700; font-size: 26px; line-height: 1.05;
    color: var(--brand-blue);
  }
  .contact-phone {
    position: absolute; right: 30px; top: 232px;
    display: flex; align-items: center; gap: 10px;
    font-size: 18px; color: var(--text-grey);
  }
  .rule {
    position: absolute; left: 30px; right: 30px; top: 266px;
    height: 1px; background: var(--rule);
  }
  .contact-row {
    position: absolute; left: 30px; right: 30px; top: 282px;
    display: flex; align-items: center; justify-content: space-between;
    font-size: 14px; color: var(--text-grey); white-space: nowrap;
  }
  .contact-item { display: flex; align-items: center; gap: 6px; }
  .divider { width: 1px; height: 16px; background: var(--text-grey); margin: 0 8px; }
  .icon { width: 15px; height: 15px; flex: none; }
</style>
</head>
<body>
<main class="stage">

  <section class="card card-back" aria-label="Card back">
    <h1 class="brand-name">Harbourline<br>Physiotherapy</h1>
  </section>

  <section class="card card-front" aria-label="Card front">
    <div class="brand">
      <span class="brand-dot"></span>
      <span class="brand-name">Harbourline<br>Physiotherapy</span>
    </div>

    <div class="contact-phone">
      <span class="phone">02 9481 2057</span>
      <svg class="icon" viewBox="0 0 16 16" aria-hidden="true">
        <path d="M3 2h3l1.5 3.5-2 1.2a8 8 0 0 0 3.8 3.8l1.2-2L14 10v3a1 1 0 0 1-1 1A11 11 0 0 1 2 3a1 1 0 0 1 1-1z" fill="var(--brand-blue)"/>
      </svg>
    </div>

    <div class="rule"></div>

    <div class="contact-row">
      <span class="contact-item">
        <span class="address">58 Wexley Lane Corvale NSW 2784</span>
        <svg class="icon" viewBox="0 0 16 16" aria-hidden="true">
          <path d="M8 1a5 5 0 0 1 5 5c0 3.5-5 9-5 9S3 9.5 3 6a5 5 0 0 1 5-5z" fill="var(--brand-blue)"/>
          <circle cx="8" cy="6" r="1.8" fill="#fff"/>
        </svg>
      </span>
      <span class="divider"></span>
      <span class="contact-item">
        <span class="email">info@harbourlinephysio.example.com.au</span>
        <svg class="icon" viewBox="0 0 16 16" aria-hidden="true">
          <rect x="1.5" y="3.5" width="13" height="9" rx="1" fill="var(--brand-blue)"/>
          <path d="M2 4l6 5 6-5" stroke="#fff" stroke-width="1.2" fill="none"/>
        </svg>
      </span>
    </div>
  </section>

</main>
</body>
</html>
```